New Business Card for Web Design/Internet Marketing Company

Looking for a great looking new business card. We are a 10 year old web design, internet marketing and website management company that works mostly with small businesses.

Our new card needs to better match the colors and style of our website, be bold, extremely usable and slightly edgy.

Target Market(s)

Small/Medium businesses that have websites

Industry/Entity Type

Internet

Requirements
Must have
• Front and back design, full color, rounded corners please

Must use the colors/style of our website (JPG provided)

INFO FOR CARDS (as readable as possible please)
Mark Lenner
President/CEO
mark@trelvanmedia.example
Phone: 520-381-7459
Toll Free: 866-381-7459
Address: 4315 W. Calloway Ave. Ste. 140, Tucson, AZ 85792

THINGS I WANT TO PROMOTE (if there is room):
1. Our Website - www.trelvanmedia.example

2. Social Media
Twitter: @trelvanmedia
Facebook: www.facebook.com/trelvanmedia

3. Our Services
Web Design
Internet Marketing
Website Management

```html
<!DOCTYPE html>
<html lang="en">
<head>
<meta charset="utf-8">
<title>Trelvan Media – Business Card</title>
<link rel="stylesheet" href="https://fonts.googleapis.com/css2?family=Source+Sans+3:wght@400;600;700&display=swap">
<style>
  :root{
    --bg:#e4e6e8;
    --brand-blue:#2a8cc4;
    --brand-orange:#f07f22;
    --ink:#2d2d2d;
    --paper:#ffffff;
    --white:#ffffff;
  }
  html,body{margin:0;padding:0;width:1200px;height:944px;overflow:hidden;background:var(--bg);}
  body{position:relative;font-family:"Source Sans 3",Arial,sans-serif;}
  .card{position:absolute;width:630px;height:360px;border-radius:16px;overflow:hidden;box-shadow:0 6px 18px rgba(0,0,0,.18);}

  /* Front */
  .card--front{left:80px;top:80px;background:var(--brand-blue);color:var(--white);}
  .edge-stripe{position:absolute;top:0;bottom:0;width:14px;background:var(--brand-orange);}
  .edge-stripe--left{left:18px;}
  .edge-stripe--right{right:18px;}
  .front-url{position:absolute;top:26px;left:0;right:0;text-align:center;font-size:17px;letter-spacing:1px;}
  .brand{display:flex;align-items:center;gap:12px;}
  .brand__dot{width:30px;height:30px;border-radius:50%;background:var(--brand-orange);flex:none;}
  .brand__name{font-weight:700;font-size:52px;line-height:1;letter-spacing:-.5px;}
  .card--front .brand{position:absolute;left:0;right:0;top:140px;justify-content:center;}
  .card--front .brand__name{color:var(--white);}
  .services{position:absolute;bottom:30px;left:0;right:0;text-align:center;font-size:19px;letter-spacing:.5px;}

  /* Back */
  .card--back{left:490px;top:500px;background:var(--paper);color:var(--ink);}
  .card--back .brand{position:absolute;left:46px;top:44px;}
  .card--back .brand__dot{width:24px;height:24px;}
  .card--back .brand__name{font-size:42px;color:var(--brand-blue);}
  .divider{position:absolute;left:46px;right:34px;top:126px;height:2px;background:var(--brand-orange);}
  .person{position:absolute;right:34px;top:138px;text-align:right;}
  .person__name{font-size:28px;color:var(--brand-orange);line-height:1.1;}
  .person__role{font-size:17px;margin-top:2px;}
  .contacts{position:absolute;left:46px;bottom:34px;margin:0;padding:0;list-style:none;font-size:15px;line-height:24px;}
  .contacts li{display:flex;align-items:center;gap:10px;}
  .contacts svg{width:15px;height:15px;flex:none;}
  .accent{color:var(--brand-orange);}
  .address{position:absolute;right:34px;bottom:34px;text-align:left;font-size:15px;line-height:22px;font-style:normal;}
</style>
</head>
<body>
  <section class="card card--front" aria-label="Card front">
    <div class="edge-stripe edge-stripe--left"></div>
    <div class="edge-stripe edge-stripe--right"></div>
    <div class="front-url">www.trelvanmedia.example</div>
    <div class="brand">
      <span class="brand__dot"></span>
      <span class="brand__name">Trelvan Media</span>
    </div>
    <div class="services">Web Design • Internet Marketing • Website Management</div>
  </section>

  <section class="card card--back" aria-label="Card back">
    <div class="brand">
      <span class="brand__dot"></span>
      <span class="brand__name">Trelvan Media</span>
    </div>
    <div class="divider"></div>
    <div class="person">
      <div class="person__name">Mark Lenner</div>
      <div class="person__role">director</div>
    </div>
    <ul class="contacts">
      <li>
        <svg viewBox="0 0 16 16" aria-hidden="true"><rect x="1" y="3" width="14" height="10" rx="1.5" fill="none" stroke="#2d2d2d" stroke-width="1.6"/><path d="M1.5 4 8 9l6.5-5" fill="none" stroke="#2d2d2d" stroke-width="1.6"/></svg>
        mark@trelvanmedia.example
      </li>
      <li>
        <svg viewBox="0 0 16 16" aria-hidden="true"><path d="M4 1.5h3l1 3.5-2 1.2a8 8 0 0 0 3.8 3.8L11 8l3.5 1v3c0 1-1 2-2 2A11.5 11.5 0 0 1 2 3.5c0-1 1-2 2-2z" fill="#2d2d2d"/></svg>
        520-381-7459
      </li>
      <li>
        <svg viewBox="0 0 16 16" aria-hidden="true"><path d="M4 1.5h3l1 3.5-2 1.2a8 8 0 0 0 3.8 3.8L11 8l3.5 1v3c0 1-1 2-2 2A11.5 11.5 0 0 1 2 3.5c0-1 1-2 2-2z" fill="#2d2d2d"/></svg>
        866-381-7459 (toll free)
      </li>
      <li>
        <svg viewBox="0 0 16 16" aria-hidden="true"><circle cx="8" cy="8" r="7" fill="#2d2d2d"/></svg>
        @trelvanmedia
      </li>
      <li>
        <svg viewBox="0 0 16 16" aria-hidden="true"><rect x="1" y="1" width="14" height="14" rx="2" fill="#2d2d2d"/></svg>
        <span>www.<span class="accent">socialpage.example</span>/trelvanmedia</span>
      </li>
    </ul>
    <address class="address">4315 W. Calloway<br>Ave. Ste. 140<br>Tucson, AZ 85792</address>
  </section>
</body>
</html>
```